We need a front cover design which can be used in conjunction with our corporate branding therefore design needs to fill 3/4 DL front page. We are a local government authority that is creating a tourism brochure promoting a number of nursery and garden centre businesses as a trail/gardeners day out. Our 6 nurseries are varied with offerings including plants, garden ware, landscaping supplies and services, cafes, a gallery space and retail spaces. Soe of our nurseries are more traditional and others very quirky including art in the garden elements. Our municipality, Brindlewood in Victoria, Australia is a balance of city and country lifestyles. We want something beautiful, eye catching and tourism related that inspires anyone with an interest in gardening, home, retail, food and lifestyle to spend a day out exploring our nurseries/garden centres. The final design needs to communicate fun, gardening, home, retail, food and lifestyle in a bright, gardeny way. This is the first trail of its type in Australia.

Reason: I have only recieved one set of designs.

Landscaping

• Petalwick Meander Route

```html
<!DOCTYPE html>
<html lang="en">
<head>
<meta charset="utf-8">
<title>Petalwick Meander Route – Cover</title>
<link rel="stylesheet" href="https://fonts.googleapis.com/css2?family=Delius&display=swap">
<style>
  :root {
    --paper: #ffffff;
    --title-teal: #72b4c0;
    --band-teal: #8ec2cb;
    --band-light: #a9d2d9;
    --band-rule: #7fb5bf;
    --ink: #161616;
    --frame: #0c0c0c;
    --mist-1: #eef1ee;
    --mist-2: #c9d3cc;
    --mist-3: #9fae9f;
    --bloom-1: #e23a5c;
    --bloom-2: #b3173b;
    --bloom-3: #f1f0d8;
    --logo-text: #ffffff;
  }
  html, body {
    margin: 0;
    padding: 0;
    overflow: hidden;
    background: var(--paper);
  }
  .cover {
    position: relative;
    width: 1200px;
    height: 2540px;
    overflow: hidden;
    background: var(--paper);
    font-family: "Delius", "Comic Sans MS", cursive;
  }
  .cover-title {
    position: absolute;
    left: 112px;
    top: 70px;
    margin: 0;
    font-weight: 400;
    font-size: 118px;
    line-height: 152px;
    color: var(--title-teal);
    letter-spacing: 1px;
  }
  .cover-title span { display: block; }
  .garden-art {
    position: absolute;
    left: 0;
    top: 0;
    width: 1200px;
    height: 2212px;
  }
  .bloom-frame {
    position: absolute;
    left: 352px;
    top: 1008px;
    width: 496px;
    height: 484px;
    background: var(--frame);
  }
  .bloom-photo {
    position: absolute;
    left: 36px;
    top: 38px;
    right: 36px;
    bottom: 38px;
    background:
      radial-gradient(circle at 52% 46%, var(--bloom-3) 0 11%, #e8d77a 13%, var(--bloom-1) 22%, #ec4f70 45%, var(--bloom-2) 78%, #6b0d22 100%);
  }
  .brand-band {
    position: absolute;
    left: 0;
    top: 2212px;
    width: 1200px;
    height: 328px;
    background: var(--band-teal);
    border-top: 20px solid var(--band-light);
    box-sizing: border-box;
  }
  .brand-band-divider {
    position: absolute;
    left: 720px;
    top: 0;
    width: 4px;
    height: 100%;
    background: var(--band-rule);
  }
  .brand-mark {
    position: absolute;
    left: 760px;
    top: 120px;
    display: flex;
    align-items: center;
    gap: 18px;
    color: var(--logo-text);
    font-size: 38px;
    letter-spacing: 3px;
    text-transform: uppercase;
  }
  .brand-mark-square {
    width: 40px;
    height: 40px;
    background: var(--logo-text);
  }
</style>
</head>
<body>
  <main class="cover">
    <h1 class="cover-title">
      <span>Petalwick</span>
      <span>Meander</span>
      <span>Route</span>
    </h1>

    <svg class="garden-art" viewBox="0 0 1200 2212" xmlns="http://www.w3.org/2000/svg">
      <defs>
        <linearGradient id="mist" x1="0" y1="1" x2="1" y2="0">
          <stop offset="0" stop-color="var(--mist-2)"/>
          <stop offset="0.35" stop-color="var(--mist-1)"/>
          <stop offset="0.6" stop-color="var(--mist-3)"/>
          <stop offset="1" stop-color="var(--mist-2)"/>
        </linearGradient>
      </defs>
      <g role="img" aria-label="Soft-focus photograph of pale blue-white flower spikes in a garden">
        <ellipse cx="600" cy="1440" rx="1050" ry="400" transform="rotate(-55 600 1440)"
                 fill="url(#mist)" stroke="var(--ink)" stroke-width="6"/>
      </g>
      <path class="brush-swoosh" fill="var(--ink)"
            d="M1140 700 C 980 800, 760 980, 620 1300 C 500 1580, 320 1900, 40 2150
               C 330 1920, 520 1600, 640 1310 C 780 990, 990 800, 1140 700 Z"/>
    </svg>

    <div class="bloom-frame">
      <div class="bloom-photo" role="img" aria-label="Close-up photograph of a bright red gerbera flower"></div>
    </div>

    <footer class="brand-band">
      <div class="brand-band-divider"></div>
      <div class="brand-mark">
        <span class="brand-mark-square"></span>
        <span>Brindlewood</span>
      </div>
    </footer>
  </main>
</body>
</html>
```